Health and Fitness Club requires a stunning and simple website

We are a health and fitness club based in Dubai, when we launch we will be the biggest club in the country, we will also have the 2 largest activity rooms in the country, we are setting a new standard in the industry by offering one thing, our attitude.

Our attitude means the following:
unlike other clubs we have no hidden charges or fees
our members can join daily, monthly, 6 months or annually
our service and facility are comparable to 5* hotel gyms
our equipment is second to none
our space is the biggest in the country
we do not force our members to use our in-house personal trainers - you can bring your own and we will not charge them entry!
we will have a cutting edge brawnmesh box in our gym with classes by the best trainers in the country
we will be providing free-lance personal trainers a platform to engage customers, grow their business and even use our activity rooms for classes

Basically we will be a gym like no other, simply because we are gym people and we hate the restrictive practices and hidden charges by other gyms, so we are making our own gym which focuses on quality and service.

All of this has to be communicated in the style of the website, the colors of the website we want to be limited to the logo colors as this will be the same theme running throughout the gym.

The landing page of the website HAS to incorporate elements from our social media presences, this basically is the usual, chirplo, snapvault, kinwall. We can have these as a sidebar, the centre of the page should display the latest article from our blog (also on the website) Also we need to have a calendar for activities and classes on the front page. The menu should have links to the following:
Latest News
About us
Team
Gallery
Membership
Classes
Member Log In
Contact Us
Location

The style of the website has to be similar to the logo, particularly in terms of the fonts used.

```html
<!DOCTYPE html>
<html lang="en">
<head>
<meta charset="utf-8">
<title>Ironhall Fitness Club</title>
<link rel="stylesheet" href="https://fonts.googleapis.com/css2?family=Oswald:wght@400;500&family=Open+Sans:ital,wght@0,400;0,600;1,400&display=swap">
<style>
:root{
  --red:#d10000;
  --red-text:#c8161d;
  --dark:#1c1d20;
  --dark-2:#3a3b40;
  --ink:#222;
  --muted:#555;
  --line:#e3e3e3;
  --white:#fff;
}
*{box-sizing:border-box;margin:0;padding:0}
html,body{width:1038px;height:1200px;overflow:hidden;background:var(--white);font-family:"Open Sans",sans-serif;color:var(--ink)}
.canvas{position:relative;width:1038px;height:1200px;overflow:hidden}
.backdrop{position:absolute;left:0;top:0;width:1038px;height:600px;background:linear-gradient(180deg,#efe6dc 0%,#d9b48c 25%,#c98a55 45%,#f3e9df 75%,#fff 100%)}
.header{position:absolute;left:63px;top:26px;width:910px;height:102px;background:linear-gradient(180deg,#3e4045,#121316);border:1px solid #000}
.brand{position:absolute;left:22px;top:30px;display:flex;align-items:center;gap:10px;font-family:"Oswald",sans-serif;font-size:24px;font-weight:500;color:var(--white);letter-spacing:1px}
.brand-dot{width:36px;height:36px;border-radius:50%;background:var(--red)}
.search{position:absolute;right:21px;top:34px;width:208px;height:38px;background:var(--white);border:3px solid #d6d8dc;border-radius:4px}
.search span{position:absolute;left:16px;top:8px;font-size:13px;color:#bbb}
.search .btn{position:absolute;right:2px;top:2px;width:30px;height:28px;background:#c5c8cd}
.nav{position:absolute;left:63px;top:143px;width:902px;height:48px;background:var(--red);display:flex;align-items:center;font-family:"Oswald",sans-serif;font-size:15px;color:var(--white)}
.nav a{color:inherit;text-decoration:none;padding:0 10px;line-height:48px}
.nav a.active{background:#202124;padding:0 22px}
.hero{position:absolute;left:63px;top:214px;width:902px;height:304px;background:linear-gradient(90deg,#c9cfd6 0%,#e9edf0 45%,#f2f2f2 60%,#d6dce2 100%)}
.dots{position:absolute;left:494px;top:272px;display:flex;gap:8px}
.dots i{width:11px;height:11px;border-radius:50%;background:var(--red)}
.dots i:first-child{background:var(--white)}
.features{position:absolute;left:63px;top:518px;width:902px;height:129px;background:linear-gradient(180deg,#3a3b40,#0f1012)}
.feature{position:absolute;top:15px;display:flex;gap:18px}
.feature .icon{width:100px;height:100px;border-radius:50%;background:#2f3035;border:2px solid #4a4b50;flex:none}
.feature h3{font-family:"Oswald",sans-serif;font-weight:500;font-size:19px;color:var(--white);margin:7px 0 12px}
.feature p{font-size:12.5px;color:#ddd;line-height:23px;width:130px}
.next{position:absolute;right:0;top:0;width:50px;height:129px;background:#3c3d44}
.social{position:absolute;left:983px;top:294px;width:55px;height:257px;background:var(--red);border-radius:6px 0 0 6px}
.social .s{position:absolute;left:10px;width:36px;height:36px;border-radius:50%;background:var(--white);border:3px solid #ddd}
.social .s b{position:absolute;left:-10px;top:36px;width:50px;text-align:center;font-size:7px;font-weight:600;color:var(--white)}
.col-title{position:absolute;font-family:"Oswald",sans-serif;font-weight:500;font-size:25px;color:var(--red-text)}
.why-photo{position:absolute;left:92px;top:735px;width:254px;height:145px;border:1px solid #ddd;padding:6px;background:var(--white)}
.why-photo div{width:100%;height:100%;background:linear-gradient(180deg,#5b7ea8,#b9cde0 60%,#6c7f96)}
.why-quote{position:absolute;left:91px;top:890px;width:270px;font-style:italic;font-size:12px;line-height:30px;color:var(--red-text)}
.why-body{position:absolute;left:90px;top:960px;width:270px;font-size:12px;line-height:28.5px;color:var(--ink)}
.article{position:absolute;left:386px;width:274px;height:126px;border-bottom:1px solid var(--line)}
.article .thumb{position:absolute;left:0;top:8px;width:73px;height:63px;border:1px solid #ddd;padding:5px;background:var(--white)}
.article .thumb div{width:100%;height:100%}
.article h4{position:absolute;left:83px;top:0;font-weight:400;font-size:14px;color:var(--red-text)}
.article p{position:absolute;left:83px;top:27px;font-size:12px;line-height:18px;color:var(--ink)}
.quote-mark{position:absolute;left:679px;top:724px;font-family:Georgia,serif;font-size:80px;line-height:80px;color:#ccc}
.testimonial{position:absolute;left:736px;top:728px;width:235px;font-size:12px;line-height:23px}
.by{position:absolute;left:878px;top:781px;font-size:12px;color:var(--red-text)}
.calendar{position:absolute;left:694px;top:841px;width:271px;border:1px solid #ddd;font-size:15px}
.cal-head{height:36px;background:linear-gradient(180deg,#3a3b40,#111);color:var(--white);text-align:center;line-height:36px;font-size:15px;font-weight:500;position:relative}
.cal-head .l,.cal-head .r{position:absolute;top:13px;width:0;height:0;border-top:5px solid transparent;border-bottom:5px solid transparent}
.cal-head .l{left:12px;border-right:6px solid #fff}
.cal-head .r{right:12px;border-left:6px solid #fff}
.cal-grid{display:grid;grid-template-columns:repeat(7,1fr)}
.cal-grid span{height:29px;line-height:29px;text-align:center;border-right:1px solid #e6e6e6;border-bottom:1px solid #e6e6e6}
.cal-grid .dn{background:var(--red);color:var(--white);height:27px;line-height:27px;font-size:14px;border-color:var(--red)}
.cal-grid .o{color:#aaa}
.cal-grid .t{background:var(--dark);color:var(--white)}
.footer{position:absolute;left:63px;top:1109px;width:902px;height:64px;background:linear-gradient(180deg,#3a3b40,#0b0b0d);color:#ddd;font-size:10.5px;text-align:center;line-height:64px}
.tag{position:absolute;left:1004px;top:1138px;font-size:11px;color:var(--red-text)}
</style>
</head>
<body>
<div class="canvas">
  <div class="backdrop" role="img" aria-label="Blurred gym interior with warm wooden ceiling and equipment"></div>

  <header class="header">
    <div class="brand"><span class="brand-dot"></span>Ironhall</div>
    <div class="search"><span>SEARCH</span><div class="btn"></div></div>
  </header>

  <nav class="nav">
    <a class="active">Home</a><a>Latest News</a><a>About us</a><a>Gallery</a><a>Membership</a><a>Classes</a><a>Member Log In</a><a>Contact Us</a><a>Location</a>
  </nav>

  <section class="hero" role="img" aria-label="Two members smiling while training on cross-trainers">
    <div class="dots"><i></i><i></i><i></i></div>
  </section>

  <section class="features">
    <div class="feature" style="left:36px"><div class="icon" role="img" aria-label="Bodybuilder silhouette icon"></div><div><h3>Bodybuilding</h3><p>Winning means you're willing to go longer,</p></div></div>
    <div class="feature" style="left:327px"><div class="icon" role="img" aria-label="Runner silhouette icon"></div><div><h3>Running</h3><p>Winning means you're willing to go longer,</p></div></div>
    <div class="feature" style="left:591px"><div class="icon" role="img" aria-label="Weight lifter silhouette icon"></div><div><h3>Weight Lifting</h3><p>Winning means you're willing to go longer,</p></div></div>
    <div class="next"><svg width="50" height="129" viewBox="0 0 50 129"><path d="M19 53 L31 65 L19 77" fill="none" stroke="#fff" stroke-width="5"/></svg></div>
  </section>

  <aside class="social">
    <div class="s" style="top:26px" aria-label="kinwall"><b>kinwall</b></div>
    <div class="s" style="top:82px" aria-label="chirplo"><b>chirplo</b></div>
    <div class="s" style="top:136px" aria-label="circlepost"><b>circlepost</b></div>
    <div class="s" style="top:192px" aria-label="snapvault"><b>snapvault</b></div>
  </aside>

  <h2 class="col-title" style="left:90px;top:673px">Why Choose us</h2>
  <div class="why-photo"><div role="img" aria-label="Row of cardio machines by large gym windows"></div></div>
  <p class="why-quote">Winning means you're willing to go longer, work harder, and give more than anyone else.</p>
  <p class="why-body">Ut enim ad minima veniam, quis nostru exercitationem ullam corporis laboriosam, nisi ut aad minima veniamliquid ex ea commodi consequatur laboriosam ipsum dolor sit amet,</p>

  <h2 class="col-title" style="left:391px;top:673px">Latest Article</h2>
  <article class="article" style="top:732px"><div class="thumb"><div role="img" aria-label="Muscular athlete torso" style="background:linear-gradient(135deg,#6b4a33,#c79a74)"></div></div><h4>Power Bodybuilding</h4><p>Sed ut perspiciatis unde omnis iste natus error sit ...</p></article>
  <article class="article" style="top:858px"><div class="thumb"><div role="img" aria-label="Woman resting after workout" style="background:linear-gradient(135deg,#9fb6c8,#e2d3c6)"></div></div><h4>Power Bodybuilding</h4><p>Sed ut perspiciatis unde omnis iste natus error sit ...</p></article>
  <article class="article" style="top:980px;height:98px"><div class="thumb"><div role="img" aria-label="Woman training on a machine" style="background:linear-gradient(135deg,#4f7fb0,#d9e2ea)"></div></div><h4>Power Bodybuilding</h4><p>Sed ut perspiciatis unde omnis iste natus error sit ...</p></article>

  <h2 class="col-title" style="left:680px;top:675px">Testimonials</h2>
  <div class="quote-mark">&ldquo;</div>
  <p class="testimonial">At one point in your life you either have the thing you want or the reasons why</p>
  <p class="by">by John Doe</p>

  <h2 class="col-title" style="left:680px;top:797px">Calendar Events</h2>
  <div class="calendar">
    <div class="cal-head"><i class="l"></i>FEBURARY 2014<i class="r"></i></div>
    <div class="cal-grid">
      <span class="dn">Su</span><span class="dn">Mo</span><span class="dn">Tu</span><span class="dn">We</span><span class="dn">Th</span><span class="dn">Fr</span><span class="dn">Sa</span>
      <span class="o">28</span><span class="o">29</span><span class="o">30</span><span class="o">31</span><span>1</span><span>2</span><span>3</span>
      <span>4</span><span>5</span><span>6</span><span>7</span><span>8</span><span>9</span><span>10</span>
      <span>11</span><span>12</span><span>13</span><span>14</span><span>15</span><span>16</span><span>17</span>
      <span>18</span><span>19</span><span class="t">20</span><span>21</span><span>22</span><span>23</span><span>24</span>
      <span>25</span><span>26</span><span>27</span><span>28</span><span></span><span></span><span class="o">1</span>
      <span class="o">2</span><span class="o">3</span><span class="o">4</span><span class="o">5</span><span class="o">6</span><span class="o">7</span><span class="o">8</span>
    </div>
  </div>

  <footer class="footer">&copy; 2014 Company Name.&nbsp; All right reserved.&nbsp; Term of Use</footer>
  <span class="tag">c3</span>
</div>
</body>
</html>
```